Business Card Re-Design/Update

We'd like to update out business cards. I've included our current "Style guide" which has the colour scheme of the organisation in it. I've also included the branding files with logos etc in them.

I've also included a copy of one of our existing cards so that you can see how ugly/dated they look. I'd like a fresh modern corporate look.

Target Market(s)

These are for our clients, potential clients, industry contacts - like all business cards

Contact Information for Business Card

Name
Position
Company Address - Level 1, 47 Fernby Street, Carlow Qld 4072
Direct Phone
mobile
Email
Website -www.korvalit.com.au
Logo

Colors

Designer to choose colors to be used in the design.

Requirements
Must have
• Main Logo
• Cards will need to be editable to be able to personalize them for each new employee.
Nice to have
• The MapOut, ShipWell, KeepSteady would be okay to have if they can be sensibly and professionally added to the look without detracting from the main imagery.
• Maybe they could go on the back of the card? will leave this to your creative discretion as to whether/where they fit.
Should not have
• Should not have decorative or script fonts

```html
<!DOCTYPE html>
<html lang="en">
<head>
<meta charset="utf-8">
<title>korvalit business card</title>
<link rel="stylesheet" href="https://fonts.googleapis.com/css2?family=Arimo:wght@400;700&display=swap">
<style>
  :root {
    --backdrop: #b4b4b4;
    --card: #3a393b;
    --red: #d7363b;
    --white: #ffffff;
    --blue: #2f8fd6;
    --green: #6bb33f;
    --purple: #b03aa0;
  }
  * { margin: 0; padding: 0; box-sizing: border-box; }
  html, body { width: 900px; height: 1200px; overflow: hidden; }
  body {
    background: var(--backdrop);
    font-family: "Arimo", Arial, sans-serif;
    color: var(--white);
    position: relative;
  }
  .card {
    position: absolute;
    left: 112px;
    width: 675px;
    height: 426px;
    background: var(--card);
    overflow: hidden;
  }
  .card--front { top: 69px; }
  .card--back { top: 628px; }
  .side-tab { position: absolute; top: 0; width: 15px; height: 426px; }
  .side-tab--left { left: 0; }
  .side-tab--right { right: 0; }

  .wordmark {
    position: absolute;
    display: flex;
    align-items: center;
    gap: 14px;
    font-weight: 400;
    color: var(--white);
    white-space: nowrap;
  }
  .wordmark__mark { background: var(--red); flex: none; }
  .card--front .wordmark { left: 155px; top: 182px; font-size: 54px; }
  .card--front .wordmark__mark { width: 48px; height: 48px; }
  .card--back .wordmark { left: 55px; top: 190px; font-size: 38px; }
  .card--back .wordmark__mark { width: 36px; height: 36px; }

  .front-web {
    position: absolute;
    left: 233px; top: 262px;
    display: flex; align-items: center; gap: 16px;
    font-size: 16px;
  }
  .front-web svg { width: 18px; height: 18px; }

  .person { position: absolute; left: 347px; top: 43px; }
  .person__name { font-size: 26px; font-weight: 700; color: var(--red); letter-spacing: 0.3px; }
  .person__role { font-size: 19px; margin-top: 4px; }

  .phone-band {
    position: absolute;
    left: 338px; width: 337px; height: 54px;
    background: var(--red);
    padding: 4px 0 0 41px;
    font-size: 17px;
    line-height: 22px;
  }
  .phone-band--personal { top: 112px; }
  .phone-band--office { top: 171px; }
  .phone-line { position: relative; }
  .phone-line svg {
    position: absolute; left: -33px; top: 3px;
    width: 15px; height: 15px;
  }

  .contact-list { position: absolute; left: 346px; top: 246px; list-style: none; font-size: 17px; }
  .contact-list li { position: relative; padding-left: 33px; line-height: 20px; margin-bottom: 10px; }
  .contact-icon {
    position: absolute; left: 0; top: 2px;
    width: 20px; height: 20px;
    background: var(--red);
    display: flex; align-items: center; justify-content: center;
  }
  .contact-icon svg { width: 12px; height: 12px; }

  .services {
    position: absolute; left: 350px; top: 380px;
    display: flex; gap: 14px;
    font-size: 17px; font-weight: 700;
  }
  .service { display: flex; align-items: center; gap: 5px; }
  .service__dot { width: 14px; height: 14px; }
  .service--ship { color: var(--blue); }
  .service--ship .service__dot { background: var(--blue); }
  .service--map { color: var(--green); }
  .service--map .service__dot { background: var(--green); }
  .service--keep { color: var(--purple); }
  .service--keep .service__dot { background: var(--purple); }
</style>
</head>
<body>

<section class="card card--front" aria-label="Card front">
  <svg class="side-tab side-tab--left" viewBox="0 0 15 426"><polygon points="0,44 15,59 15,367 0,382" fill="var(--red)"/></svg>
  <svg class="side-tab side-tab--right" viewBox="0 0 15 426"><polygon points="15,44 0,59 0,367 15,382" fill="var(--red)"/></svg>
  <div class="wordmark"><span class="wordmark__mark"></span>korvalit</div>
  <div class="front-web">
    <svg viewBox="0 0 20 20" fill="none" stroke="#fff" stroke-width="1.5"><circle cx="10" cy="10" r="8.5"/><ellipse cx="10" cy="10" rx="4" ry="8.5"/><line x1="1.5" y1="10" x2="18.5" y2="10"/><line x1="3" y1="5.5" x2="17" y2="5.5"/><line x1="3" y1="14.5" x2="17" y2="14.5"/></svg>
    <span>www.korvalit.com.au</span>
  </div>
</section>

<section class="card card--back" aria-label="Card back">
  <svg class="side-tab side-tab--left" viewBox="0 0 15 426"><polygon points="0,44 15,59 15,367 0,382" fill="var(--red)"/></svg>
  <div class="wordmark"><span class="wordmark__mark"></span>korvalit</div>

  <div class="person">
    <p class="person__name">DANA WHITFIELD</p>
    <p class="person__role">Business Development Manager</p>
  </div>

  <div class="phone-band phone-band--personal">
    <p class="phone-line"><svg viewBox="0 0 16 16" fill="none" stroke="#fff" stroke-width="1.5"><rect x="4" y="1" width="8" height="14" rx="1.5"/><line x1="7" y1="12.5" x2="9" y2="12.5"/></svg>+61 (0)412 555 018</p>
    <p class="phone-line"><svg viewBox="0 0 16 16" fill="#fff"><path d="M3 1.5l3 3-1.5 2a9 9 0 0 0 5 5l2-1.5 3 3-2 2C7 14.5 1.5 9 1 3.5z"/></svg>+61 (0)7 3555 0142</p>
  </div>
  <div class="phone-band phone-band--office">
    <p class="phone-line"><svg viewBox="0 0 16 16" fill="#fff"><path d="M1 6c2-3 12-3 14 0l-1 2-3-1V5.5H5V7L2 8z"/><rect x="3" y="9" width="10" height="6" rx="1"/></svg>+61 (0)7 3555 0100</p>
    <p class="phone-line"><svg viewBox="0 0 16 16" fill="#fff"><rect x="4" y="1" width="8" height="5"/><rect x="1" y="7" width="14" height="8" rx="1"/></svg>+61 (0)7 3555 0199</p>
  </div>

  <ul class="contact-list">
    <li><span class="contact-icon"><svg viewBox="0 0 12 12" fill="var(--card)"><path d="M6 0a4 4 0 0 1 4 4c0 3-4 8-4 8S2 7 2 4a4 4 0 0 1 4-4zm0 2.5a1.5 1.5 0 1 0 0 3 1.5 1.5 0 0 0 0-3z"/></svg></span>Level 1, 47 Fernby Street, Carlow<br>Qld 4072</li>
    <li><span class="contact-icon"><svg viewBox="0 0 12 12" fill="var(--card)"><path d="M0 2h12v8H0z"/><path d="M0 2l6 5 6-5" fill="none" stroke="var(--red)" stroke-width="1"/></svg></span>whitfield@korvalit.com.au</li>
    <li><span class="contact-icon"><svg viewBox="0 0 12 12" fill="none" stroke="var(--card)" stroke-width="1.2"><circle cx="6" cy="6" r="5"/><ellipse cx="6" cy="6" rx="2.3" ry="5"/><line x1="1" y1="6" x2="11" y2="6"/></svg></span>www.korvalit.com.au</li>
  </ul>

  <div class="services">
    <span class="service service--ship"><span class="service__dot"></span>ShipWell</span>
    <span class="service service--map"><span class="service__dot"></span>MapOut</span>
    <span class="service service--keep"><span class="service__dot"></span>KeepSteady</span>
  </div>
</section>

</body>
</html>
```